Premium CBD/Hemp company needs packaging and label design

Quillmore Apothecare, a premium CBD/Hemp company based in Scottsdale, Arizona is in need of a packaging and label design. We are launching with our flagship product which will be a 30 count capsule and will come in three functions: Pain Relief, Anxiety Support, and Sleep Support. For the purpose of this contest, please design packaging and label for our Anxiety Support product. Our products are physician formulated and all natural. Our main ingredient is CBD/Hemp and is complemented by specific herbs that synergistically work together to give the customer the most effective and desired result. We would like our branding to have a pharmaceutical look and feel with a focus on trust and transparency. We have uploaded our company logo that is to be used on both the packaging and label. We have also uploaded an executed branding questionnaire that will guide you to exactly what we are seeking to achieve as to the look and feel of our brand. Please feel free to contact us with any questions that you may have. The winner of this contest will have the opportunity to work with us on future projects as we will need packaging and label design for our entire Quillmore Apothecare product line.

Target Market(s)

See attached branding questionnaire

Industry/Entity Type

Health And Wellness

Font styles to use
Sans Serif

Colors

Designer to choose colors to be used in the design.

Requirements
Must have
• See attached branding questionnaire; Please superimpose labels onto a cobalt blue capsule bottle (see attached)
• >>UPON REVIEW of the FIRST 8 designs, we really like the silver, mildly metallic label background in DESIGN # 21300528, we do not want metalic lettering as that would not look very "Pharmaceutical"
• >>We are in search of a look that is a bit more "Pharmaceutical" than a look that would be more commonly found in a Supplement Store
Nice to have
• "See attached branding questionnaire
Should not have
• See attached branding questionnaire; NO marijuana or cannabis plant on the packaging or label

```html
<!DOCTYPE html>
<html lang="en">
<head>
<meta charset="utf-8">
<title>Quillmore Apothecare – Anxiety Support Packaging</title>
<link href="https://fonts.googleapis.com/css2?family=Encode+Sans+Condensed:wght@300;400;600&family=Roboto+Mono:wght@500&display=swap" rel="stylesheet">
<style>
  :root {
    --bg: #e4e5e6;
    --paper: #f4f4f4;
    --paper-edge: #d9d9d9;
    --ink: #3a3a3a;
    --rule: #555555;
    --badge: #4a4a4a;
    --navy: #1f3b8c;
    --teal-blue: #1f4f8a;
    --green: #1c8a48;
    --side-ink: #3b4a7a;
  }
  * { margin: 0; padding: 0; box-sizing: border-box; }
  html, body { width: 1200px; height: 1090px; overflow: hidden; }
  body {
    background: var(--bg);
    font-family: "Encode Sans Condensed", "Arial Narrow", sans-serif;
    color: var(--ink);
    position: relative;
  }

  /* ---------- Box: side panel ---------- */
  .box-side {
    position: absolute; left: 150px; top: 260px;
    width: 140px; height: 560px;
    background: #ececec;
    border: 1px solid var(--paper-edge);
    padding: 22px 14px;
    color: var(--side-ink);
    font-size: 8px; line-height: 1.45;
  }
  .box-side h4 { font-size: 8px; font-weight: 600; margin-top: 12px; }
  .box-side h4:first-child { margin-top: 0; }
  .best-before {
    position: absolute; left: 14px; top: 392px; width: 112px;
    font-size: 7px; font-weight: 600; letter-spacing: .02em; line-height: 1.3;
  }
  .batch-box {
    position: absolute; left: 14px; top: 420px;
    width: 110px; height: 110px;
    border: 1px solid #8a94b8; border-radius: 8px;
    padding: 12px 8px; font-size: 8px; line-height: 2.8;
  }

  /* ---------- Box: front panel ---------- */
  .box-front {
    position: absolute; left: 290px; top: 260px;
    width: 340px; height: 560px;
    background: var(--paper);
    border: 1px solid var(--paper-edge);
  }
  .box-front .hero {
    position: absolute; left: 72px; top: 28px;
    width: 196px; height: 310px;
  }

  /* ---------- Shared product block ---------- */
  .product-title {
    display: inline-block;
    border-top: 1.5px solid var(--rule);
    border-bottom: 1.5px solid var(--rule);
    padding: 4px 0 2px;
    font-weight: 300;
    font-size: 44px; line-height: 0.95;
    letter-spacing: .01em;
    color: var(--ink);
  }
  .pack-badge {
    display: inline-flex; align-items: center;
    background: var(--badge); color: #fff;
    font-family: "Roboto Mono", monospace; font-weight: 500;
    font-size: 11px; padding: 4px 5px; margin-top: 12px;
  }
  .pack-badge .sep { width: 1px; height: 13px; background: #fff; margin: 0 6px; }
  .title-block { position: absolute; text-align: left; }
  .box-front .title-block { left: 100px; top: 366px; }

  .brand {
    position: absolute; display: flex; align-items: center; gap: 8px;
    color: var(--navy); font-weight: 400; white-space: nowrap;
  }
  .brand .dot {
    width: 26px; height: 26px; border-radius: 50%;
    border: 2px solid var(--navy);
  }
  .box-front .brand { left: 88px; top: 516px; font-size: 19px; }

  /* ---------- Bottle label ---------- */
  .bottle-label {
    position: absolute; left: 720px; top: 300px;
    width: 330px; height: 440px;
    background: #ffffff;
    border-radius: 18px;
    box-shadow: 0 0 0 1px #d4d4d4;
  }
  .bottle-label .hero {
    position: absolute; left: 100px; top: 28px;
    width: 130px; height: 130px;
  }
  .bottle-label .title-block { left: 92px; top: 180px; }
  .bottle-label .brand { left: 104px; top: 372px; font-size: 15px; }
  .bottle-label .brand .dot { width: 22px; height: 22px; }
</style>
</head>
<body>

  <section class="box-side" aria-label="Box side panel">
    <h4>Quillmore Apothecare</h4>
    <p>Address: 14 Larkspur Row, Suite 2, Fenwick Valley</p>
    <h4>Customer Care:</h4>
    <p>Tel No.: +1 555 014 2290</p>
    <p>Email: care@quillmore.example</p>
    <h4>For more details visit:</h4>
    <p>www.quillmore.example</p>
    <h4>Manufactured by:</h4>
    <p>Address: 88 Ardent Lane, Hollow Bay</p>
    <p class="best-before">BEST BEFORE 24 MONTHS FROM MANUFACTURE</p>
    <div class="batch-box">
      <p>Batch No.:</p>
      <p>Mfg. Date:</p>
      <p>Cost:</p>
    </div>
  </section>

  <section class="box-front" aria-label="Box front panel">
    <svg class="hero" viewBox="0 0 196 310" role="img" aria-label="Illustration of a head in profile with radiating rays, blue to green">
      <defs>
        <linearGradient id="heroFadeBox" x1="0" y1="0" x2="0" y2="1">
          <stop offset="0" stop-color="#1f4f8a"/>
          <stop offset="1" stop-color="#1c8a48"/>
        </linearGradient>
      </defs>
      <path d="M0 0 H196 V212 A98 98 0 0 1 0 212 Z" fill="url(#heroFadeBox)"/>
    </svg>
    <div class="title-block">
      <div class="product-title">ANXIETY<br>SUPPORT</div><br>
      <div class="pack-badge">30 CAPSULES<span class="sep"></span>100gm</div>
    </div>
    <div class="brand"><span class="dot"></span>Quillmore Apothecare</div>
  </section>

  <section class="bottle-label" aria-label="Bottle label">
    <svg class="hero" viewBox="0 0 130 130" role="img" aria-label="Illustration of a head in profile within a ring of rays, blue to green">
      <defs>
        <linearGradient id="heroFadeLabel" x1="0" y1="0" x2="0" y2="1">
          <stop offset="0" stop-color="#1f4f8a"/>
          <stop offset="1" stop-color="#1c8a48"/>
        </linearGradient>
      </defs>
      <circle cx="65" cy="65" r="64" fill="url(#heroFadeLabel)"/>
    </svg>
    <div class="title-block">
      <div class="product-title">ANXIETY<br>SUPPORT</div><br>
      <div class="pack-badge">30 CAPSULES<span class="sep"></span>100gm</div>
    </div>
    <div class="brand"><span class="dot"></span>Quillmore Apothecare</div>
  </section>

</body>
</html>
```